New Business Card Design Project

I need a design for business cards, i am an electrical business called "Corvane Electrical and Communications" i need the cards to be double sided with the company logo on the back (attached) the front needs to say my company name, web site, email address, telephone number, and ABN number and electrical license number. I am open to different arrangements of the information but would like the background to be incorporating something electrical or something that looks smart. open to all additional ideas also.

The company colours are orange and grey see logo attached.

Business Name: Corvane Electrical and Communications
Website: corvaneelectricalandcomms.example.com.au
Email: brent@corvaneelectricalandcomms.example.com.au
Telephone(mobile): 0481209736
ABN: 71208349162
Lic No: 418273D

Target Market(s)

Business entities, Project Managers, Accounts, Clients

Industry/Entity Type

Electrician

Contact Information for Business Card

I need a design for business cards, i am an electrical business called "Corvane Electrical and Communications" i need the cards to be double sided with the company logo on the back (attached) the front needs to say my company name

Font styles to use
Serif
Sans Serif

Colors
f37122
5c5c5c

Requirements
Must have
• Must have the Logo on the back open to different ways of it being on the back but had in mind to keep it central but again open to other options
Nice to have
• A real modern cool background that is eye catching yet contemporary
Should not have
• No backgrounds of a light bulb or plug or anything like that

```html
<!DOCTYPE html>
<html lang="en">
<head>
<meta charset="utf-8">
<title>Corvane Electrical and Communications – Business Cards</title>
<link rel="stylesheet" href="https://fonts.googleapis.com/css2?family=Mulish:wght@400;600;700&display=swap">
<style>
  :root {
    --stage: #e9e7e3;
    --card-grey: #5c5c5c;
    --card-grey-dark: #4f4f4f;
    --card-white: #f7f7f7;
    --accent: #f2b91c;
    --ink-grey: #5f5f5f;
    --ink-white: #ffffff;
    --muted-white: #e6e6e6;
  }
  * { box-sizing: border-box; margin: 0; padding: 0; }
  html, body {
    width: 1200px; height: 780px; overflow: hidden;
    background: var(--stage);
    font-family: "Mulish", Arial, sans-serif;
  }
  .canvas {
    position: relative; width: 1200px; height: 780px;
    display: flex; align-items: center; justify-content: center; gap: 40px;
  }
  .card {
    position: relative; width: 540px; height: 310px;
    border-radius: 4px; overflow: hidden;
    box-shadow: 0 10px 24px rgba(0,0,0,0.18);
  }
  .card-bg { position: absolute; inset: 0; }

  /* Front */
  .brand-name {
    position: absolute; left: 28px; top: 70px; width: 190px;
    color: var(--ink-grey); font-weight: 700; font-size: 21px; line-height: 1.2;
  }
  .brand-mark {
    display: inline-block; width: 12px; height: 12px; border-radius: 50%;
    background: var(--accent); margin-bottom: 10px;
  }
  .registration {
    position: absolute; left: 28px; bottom: 30px;
    font-size: 13px; line-height: 1.6; color: var(--ink-grey);
  }
  .registration .label { color: var(--accent); font-weight: 600; }

  .person {
    position: absolute; left: 252px; top: 44px; color: var(--ink-white);
  }
  .person-name { font-size: 22px; font-weight: 700; letter-spacing: 0.2px; }
  .person-role { font-size: 14px; color: var(--accent); font-weight: 600; margin-top: 2px; }

  .contact-list {
    position: absolute; left: 252px; bottom: 40px; list-style: none;
    font-size: 10px; color: var(--muted-white);
  }
  .contact-item { display: flex; align-items: center; gap: 8px; margin-top: 9px; }
  .contact-icon {
    flex: none; width: 16px; height: 16px; border-radius: 2px;
    background: var(--accent); display: flex; align-items: center; justify-content: center;
  }
  .contact-icon svg { width: 10px; height: 10px; }

  /* Back */
  .card--back { background: linear-gradient(135deg, var(--card-grey) 0%, var(--card-grey-dark) 100%); }
  .back-brand {
    position: absolute; inset: 0; display: flex; flex-direction: column;
    align-items: center; justify-content: center; text-align: center;
    color: var(--ink-white); font-weight: 700; font-size: 28px; line-height: 1.25;
  }
  .back-brand .brand-mark { width: 14px; height: 14px; margin-bottom: 14px; }
</style>
</head>
<body>
<main class="canvas">

  <section class="card card--front" aria-label="Business card front">
    <svg class="card-bg" viewBox="0 0 540 310" preserveAspectRatio="none" aria-hidden="true">
      <rect width="540" height="310" fill="var(--card-grey)"/>
      <path d="M0 0 H210 C250 90 235 220 190 310 H0 Z" fill="var(--card-white)"/>
      <path d="M210 0 C250 90 235 220 190 310" fill="none" stroke="var(--accent)" stroke-width="4"/>
      <path d="M196 0 C236 90 221 220 176 310" fill="none" stroke="#dcdcdc" stroke-width="1"/>
    </svg>

    <div class="brand-name">
      <span class="brand-mark"></span><br>
      Corvane<br>Electrical &amp;<br>Communications
    </div>

    <p class="registration">
      <span class="label">Lic No:</span> 418273D<br>
      <span class="label">ABN:</span> 71208349162
    </p>

    <div class="person">
      <p class="person-name">Employee Name</p>
      <p class="person-role">Principal</p>
    </div>

    <ul class="contact-list">
      <li class="contact-item">
        <span class="contact-icon"><svg viewBox="0 0 10 10"><path d="M2 1 L4 1 L4.6 3 L3.6 3.8 C4.2 5 5 5.8 6.2 6.4 L7 5.4 L9 6 L9 8 C5 8.5 1.5 5 2 1 Z" fill="var(--card-grey)"/></svg></span>
        0481209736
      </li>
      <li class="contact-item">
        <span class="contact-icon"><svg viewBox="0 0 10 10"><rect x="1" y="2.5" width="8" height="5.5" fill="none" stroke="var(--card-grey)" stroke-width="1"/><path d="M1 2.5 L5 5.5 L9 2.5" fill="none" stroke="var(--card-grey)" stroke-width="1"/></svg></span>
        brent@corvaneelectricalandcomms.example.com.au
      </li>
      <li class="contact-item">
        <span class="contact-icon"><svg viewBox="0 0 10 10"><circle cx="5" cy="5" r="3.8" fill="none" stroke="var(--card-grey)" stroke-width="1"/><ellipse cx="5" cy="5" rx="1.6" ry="3.8" fill="none" stroke="var(--card-grey)" stroke-width="0.8"/><path d="M1.2 5 H8.8" stroke="var(--card-grey)" stroke-width="0.8"/></svg></span>
        corvaneelectricalandcomms.example.com.au
      </li>
    </ul>
  </section>

  <section class="card card--back" aria-label="Business card back">
    <div class="back-brand">
      <span class="brand-mark"></span>
      Corvane<br>Electrical &amp; Communications
    </div>
  </section>

</main>
</body>
</html>
```